Design a card that will be used for an e-gift card sold to customers.

I need to design the front an e-gift card for my pizza store. I picked the business card because it fits the same size as an e-gift card. I need the design and then I will submit to e-gift card company to produce. Looking for a fresh look that will appear cool, trendy to customer. Prefer to keep it to black and white but can add a bright green color.

Target Market(s)

My pizza store customers

Industry/Entity Type

Business

Contact Information for Business Card

I want the name Golden Hearth Pizza

Font styles to use
Sans Serif

Colors
9bcb3c

Requirements
Must have
• Golden Hearth Pizza
• Cedar Hollow
Nice to have
• I would like a black background. Maybe Golden Hearth Pizza in white and the location, Cedar Hollow. Maybe faded in background are words like, pizza, salads, wings, pepperoni, etc...or cartoon type pictures like pizza slices, fun pics. Would like to keep black and white shades but other colors are lighter greens.

```html
<!DOCTYPE html>
<html lang="en">
<head>
<meta charset="utf-8">
<title>Golden Hearth Pizza – Gift Card</title>
<link href="https://fonts.googleapis.com/css2?family=Oswald:wght@400&family=Source+Sans+3:wght@400&display=swap" rel="stylesheet">
<style>
  :root {
    --page-bg: #e9e9eb;
    --card-bg: #1f2a35;
    --lime: #bdf441;
    --white: #ffffff;
    --rule: #8a939c;
  }
  html, body {
    margin: 0;
    width: 1200px;
    height: 900px;
    overflow: hidden;
    background: var(--page-bg);
  }
  .gift-card {
    position: absolute;
    left: 120px;
    top: 154px;
    width: 960px;
    height: 592px;
    background: var(--card-bg);
    box-shadow: 0 10px 30px rgba(0, 0, 0, 0.18);
  }
  .brand-name {
    position: absolute;
    left: 0;
    right: 0;
    top: 150px;
    margin: 0;
    text-align: center;
    font-family: "Oswald", "Arial Narrow", sans-serif;
    font-weight: 400;
    font-size: 92px;
    line-height: 1.1;
    letter-spacing: 3px;
    color: var(--white);
    text-transform: uppercase;
    white-space: nowrap;
  }
  .location-divider {
    position: absolute;
    left: 195px;
    top: 412px;
    width: 565px;
    height: 52px;
  }
  .location {
    position: absolute;
    left: 0;
    right: 0;
    top: 486px;
    margin: 0;
    text-align: center;
    font-family: "Source Sans 3", "Helvetica", sans-serif;
    font-size: 40px;
    color: var(--white);
  }
</style>
</head>
<body>
  <main class="gift-card">
    <h1 class="brand-name">Golden Hearth Pizza</h1>

    <svg class="location-divider" viewBox="0 0 565 52" aria-hidden="true">
      <line x1="0" y1="26" x2="268" y2="26" stroke="var(--rule)" stroke-width="1.5"/>
      <line x1="297" y1="26" x2="565" y2="26" stroke="var(--rule)" stroke-width="1.5"/>
      <path d="M282.5 8 a12 12 0 0 1 12 12 c0 9 -12 24 -12 24 c0 0 -12 -15 -12 -24 a12 12 0 0 1 12 -12 z"
            fill="var(--lime)"/>
      <circle cx="282.5" cy="20" r="4.5" fill="var(--card-bg)"/>
    </svg>

    <p class="location">Cedar Hollow</p>
  </main>
</body>
</html>
```